Harborview Estates Business Card for Apartment Buildings

Create business cards for resident managers who run apartment buildings. The audience is the public who are searching for apartment rentals, and current residents who live at the apartment building. Key design element will be incorporating the company logo, however, the logo cannot dominate. The building name and manager name are more important than the logo. Current business card design leaves little room for copy, so we may need to reduce the size on the current card to allow for more space for copy.

Target Market(s)

Adults 18-65 years of age, who are looking for an apartment rental, plus current residents who live at our apartment buildings.

Industry/Entity Type

Property Management

Contact Information for Business Card

A major design element will be use of the company logo. Important property and manager contact information must be part of the design. The size of the logo will need to be reduced to make room for building and manager contact copy.

Font styles to use
Sans Serif

Colors
3176b5
000000
959595
ffffff

Requirements
Must have
• 1) Incorporate the company logo.
• 2) Use the company colors (dark blue, black/grey, over white).
• 3) FEATURE THE BUILDING NAME
• 4) FEATURE THE MANAGER NAME
• 5) The company name is less important than BUILDING and MANAGER
• 6) Manager contact information
• **SEE ATTACHED CREATIVE BRIEF**
Nice to have
• 1) Back of card logo watermark
• 2) Ability to write notes on back of carfd
Should not have
• Avoid letting the company logo dominate the card, the building name and manager are more important than the company logo.

```html
<!DOCTYPE html>
<html lang="en">
<head>
<meta charset="UTF-8">
<title>Harborview Estates – Resident Manager Business Card</title>
<link href="https://fonts.googleapis.com/css2?family=Lato:wght@400;700;900&display=swap" rel="stylesheet">
<style>
  :root {
    --brand-blue: #1669ad;
    --brand-blue-deep: #0f5c9c;
    --ink: #2b2b2b;
    --band-grey: #4a4a4c;
    --muted: #959595;
    --paper: #ffffff;
    --backdrop: #e9ebee;
  }
  * { margin: 0; padding: 0; box-sizing: border-box; }
  html, body { width: 1200px; height: 900px; overflow: hidden; }
  body {
    background: var(--backdrop);
    font-family: "Lato", Arial, sans-serif;
    position: relative;
  }
  .card {
    position: absolute;
    left: 260px;
    width: 680px;
    height: 388px;
    border-radius: 20px;
    overflow: hidden;
    box-shadow: 0 6px 18px rgba(0,0,0,0.18);
  }

  /* Back of card */
  .card-back { top: 40px; background: var(--brand-blue); color: var(--paper); }
  .card-back .company-mark {
    position: absolute; top: 130px; left: 0; width: 100%;
    display: flex; align-items: center; justify-content: center; gap: 18px;
  }
  .company-mark .mark-square { width: 46px; height: 46px; background: currentColor; }
  .company-mark .company-name {
    font-weight: 900; font-size: 50px; letter-spacing: 1px; line-height: 1; text-transform: uppercase;
  }
  .card-back .back-web {
    position: absolute; bottom: 44px; width: 100%; text-align: center;
    font-size: 19px; letter-spacing: 1.5px;
  }

  /* Front of card */
  .card-front { top: 472px; background: var(--paper); }
  .card-front .company-mark {
    position: absolute; top: 34px; left: 0; width: 100%;
    display: flex; align-items: center; justify-content: center; gap: 14px;
    color: var(--brand-blue);
  }
  .card-front .company-mark .mark-square { width: 30px; height: 30px; }
  .card-front .company-mark .company-name { font-size: 34px; }
  .manager {
    position: absolute; top: 98px; left: 0; width: 100%; text-align: center;
  }
  .manager-name { color: var(--brand-blue); font-weight: 700; font-size: 31px; }
  .manager-title { color: var(--ink); font-size: 19px; margin-top: 2px; }
  .divider {
    position: absolute; top: 176px; left: 34px; right: 34px;
    height: 2px; background: var(--brand-blue);
  }
  .contact-list { position: absolute; top: 192px; left: 40px; list-style: none; }
  .contact-list li {
    display: flex; align-items: center; gap: 14px;
    font-size: 21px; color: var(--ink); height: 31px;
  }
  .contact-list svg { width: 16px; height: 16px; fill: var(--brand-blue); }
  .property {
    position: absolute; top: 196px; right: 40px; text-align: right;
  }
  .property-name { color: var(--brand-blue); font-weight: 700; font-size: 26px; }
  .property-address { color: var(--ink); font-size: 21px; line-height: 1.3; margin-top: 4px; }
  .email-band {
    position: absolute; left: 0; right: 0; top: 300px; height: 40px;
    background: var(--band-grey); color: var(--paper);
    text-align: center; font-size: 21px; line-height: 40px;
  }
  .web-band {
    position: absolute; left: 0; right: 0; top: 340px; bottom: 0;
    background: var(--brand-blue); color: var(--paper);
    text-align: center; font-size: 21px; line-height: 48px;
  }
</style>
</head>
<body>

  <section class="card card-back">
    <div class="company-mark">
      <span class="mark-square"></span>
      <span class="company-name">Harborview Estates</span>
    </div>
    <p class="back-web">www.harborviewestates.com</p>
  </section>

  <section class="card card-front">
    <div class="company-mark">
      <span class="mark-square"></span>
      <span class="company-name">Harborview Estates</span>
    </div>

    <div class="manager">
      <p class="manager-name">Marisol Delgado</p>
      <p class="manager-title">Resident Manager</p>
    </div>

    <div class="divider"></div>

    <ul class="contact-list">
      <li>
        <svg viewBox="0 0 16 16" aria-label="Phone"><path d="M4 1 L6.5 4.5 L5 6 C6 8.5 7.5 10 10 11 L11.5 9.5 L15 12 L13 15 C7 14.5 1.5 9 1 3 Z"/></svg>
        555-210-4471
      </li>
      <li>
        <svg viewBox="0 0 16 16" aria-label="Fax"><rect x="4" y="1" width="8" height="5"/><rect x="1" y="6" width="14" height="6" rx="1"/><rect x="4" y="11" width="8" height="4"/></svg>
        555-210-4472
      </li>
      <li>
        <svg viewBox="0 0 16 16" aria-label="Mobile"><path d="M4 0 H12 V16 H4 Z M5.5 2 V12 H10.5 V2 Z"/><circle cx="8" cy="14" r="0.9" fill="#fff"/></svg>
        555-384-9063
      </li>
    </ul>

    <div class="property">
      <p class="property-name">Cedar Grove Apartments</p>
      <p class="property-address">2418 Larkspur Avenue<br>Fairmont, CA 90417</p>
    </div>

    <div class="email-band">email: marisol@harborviewestates.com</div>
    <div class="web-band">www.harborviewestates.com</div>
  </section>

</body>
</html>
```